Harrow Grading LLC business card design

Excavation company business cards

Contact Information for Business Card

Harrow Grading LLC cell phone 208-417-6290 office phone 208-319-4856 harrowgradingllc@maplecove.com Driveways, site prep, retaining walls, septic systems, rock delivery

Colors

Designer to choose colors to be used in the design.

```html
<!DOCTYPE html>
<html lang="en">
<head>
<meta charset="UTF-8">
<title>Harrow Grading LLC – Business Card</title>
<link href="https://fonts.googleapis.com/css2?family=Arimo:wght@400;700&family=Michroma&display=swap" rel="stylesheet">
<style>
  :root {
    --orange: #e86c1f;
    --orange-soft: #f6b58a;
    --white: #ffffff;
    --slate: #666666;
    --ink: #555555;
    --backdrop: #c4c4c4;
  }
  * { margin: 0; padding: 0; box-sizing: border-box; }
  html, body {
    width: 1200px; height: 800px; overflow: hidden;
    background: var(--backdrop);
    font-family: "Arimo", Arial, sans-serif;
  }
  .stage { position: relative; width: 1200px; height: 800px; }
  .card {
    position: absolute; left: 320px;
    width: 560px; height: 320px;
    border-radius: 16px; overflow: hidden;
    box-shadow: 0 10px 28px rgba(0,0,0,0.25);
  }
  /* Front */
  .card-front { top: 50px; background: var(--white); }
  .corner-accent {
    position: absolute; right: 0; top: 0; width: 150px; height: 90px;
    background: var(--slate);
    clip-path: polygon(0 0, 100% 0, 100% 100%);
  }
  .front-band {
    position: absolute; left: 0; right: 0; top: 168px; height: 112px;
    background: var(--orange);
  }
  .front-art {
    position: absolute; right: 24px; top: 28px; width: 190px; height: 222px;
    border-radius: 22px;
    border: 6px solid var(--white);
    background: linear-gradient(150deg, var(--orange-soft) 0%, var(--orange) 70%);
  }
  .person { position: absolute; left: 40px; top: 84px; }
  .person-name {
    font-family: "Michroma", Arial, sans-serif;
    color: var(--orange); font-size: 20px; letter-spacing: 1px;
  }
  .person-title { color: var(--ink); font-size: 14px; margin-top: 4px; }
  .contact-list {
    position: absolute; left: 40px; top: 184px; list-style: none;
    color: var(--white); font-size: 15px;
  }
  .contact-list li { display: flex; align-items: center; gap: 10px; height: 26px; }
  .contact-list svg { width: 16px; height: 16px; flex: none; }
  /* Back */
  .card-back { top: 430px; background: var(--orange); }
  .brand {
    position: absolute; left: 0; right: 0; top: 100px;
    display: flex; justify-content: center; align-items: center; gap: 14px;
    color: var(--white); font-weight: 700; font-size: 38px; letter-spacing: 1px;
  }
  .brand-mark { width: 24px; height: 24px; background: var(--white); }
  .services-band {
    position: absolute; left: 0; right: 0; top: 236px; height: 40px;
    background: var(--slate); color: var(--white);
    display: flex; align-items: center; justify-content: center;
    font-size: 16px;
  }
</style>
</head>
<body>
<main class="stage">
  <section class="card card-front">
    <div class="corner-accent"></div>
    <div class="front-band"></div>
    <div class="front-art" role="img" aria-label="Illustration of an excavator arm and bucket"></div>
    <div class="person">
      <div class="person-name">MARCUS HALDEN</div>
      <div class="person-title">Managing Director</div>
    </div>
    <ul class="contact-list">
      <li>
        <svg viewBox="0 0 16 16" aria-hidden="true"><rect x="4" y="1" width="8" height="14" rx="1.5" fill="none" stroke="#fff" stroke-width="1.5"/><circle cx="8" cy="12.5" r="0.9" fill="#fff"/></svg>
        208-417-6290
      </li>
      <li>
        <svg viewBox="0 0 16 16" aria-hidden="true"><path d="M4 1.5l2.5 3-1.5 1.8c.8 1.8 2.2 3.2 4 4l1.8-1.5 3 2.5-1.6 2.4C7 13.5 2.5 9 1.7 3.1z" fill="#fff"/></svg>
        208-319-4856
      </li>
      <li>
        <svg viewBox="0 0 16 16" aria-hidden="true"><rect x="1" y="3.5" width="14" height="9" fill="#fff"/><path d="M1 3.5l7 5 7-5" fill="none" stroke="#e86c1f" stroke-width="1.2"/></svg>
        harrowgradingllc@maplecove.com
      </li>
    </ul>
  </section>

  <section class="card card-back">
    <div class="brand">
      <span class="brand-mark"></span>
      <span class="brand-name">Harrow Grading LLC</span>
    </div>
    <div class="services-band">Driveways | Site prep | Retaining walls | Septic systems | Rock delivery</div>
  </section>
</main>
</body>
</html>
```